Stylish Business Cards Wanted

- DOUBLE SIDED Design Required -

High end, edgy cards for a corporate and personal stylist. Must include logo,
Name: Belinda Harwick
Title: Director and Stylist
telephone : +61 8 7142 5809
email: belinda@theloombriefing.example
website: theloombriefing.example
Tag: Corporate Workwear & Uniform Specialist | Personal Stylist
Would like nice icons for telephone, email, website

Target Market(s)

Businesses wanting stylish uniforms, people wanting stylish wardrobes

Industry/Entity Type

Corporate Workwear Stylist

Contact Information for Business Card

I would like black, white and gold foiling incorporated in the design - possibly a touch of the other colours on my branding guide attached Name: Belinda Harwick Title: Director and Stylist telephone : +61 8 7142 5809 email: belinda@theloombriefing.example website: theloombriefing.example Tag: Corporate Workwear & Uniform Specialist | Personal Stylist Would like nice icons for telephone, email, website

Font styles to use
Other font styles liked:
• Raleway

Colors

Designer to choose colors to be used in the design.

Requirements
Must have
• Gold foil accents

```html
<!DOCTYPE html>
<html lang="en">
<head>
<meta charset="utf-8">
<title>The Loom Briefing – Business Card</title>
<link rel="stylesheet" href="https://fonts.googleapis.com/css2?family=Cinzel:wght@700&family=Open+Sans:wght@400;600&display=swap">
<style>
  :root {
    --backdrop: #cbcbcb;
    --card-white: #ffffff;
    --gold: #e3bf60;
    --ink: #111111;
    --text-dark: #3a3a3a;
    --icon-dark: #333333;
    --paper: #ffffff;
  }
  html, body {
    margin: 0;
    padding: 0;
    width: 1200px;
    height: 1035px;
    overflow: hidden;
    background: var(--backdrop);
    font-family: "Open Sans", Arial, sans-serif;
  }
  .canvas {
    position: relative;
    width: 1200px;
    height: 1035px;
  }
  .card {
    position: absolute;
    width: 560px;
    height: 320px;
    overflow: hidden;
    box-shadow: 0 14px 30px rgba(0,0,0,0.22);
  }
  .card--front { left: 110px; top: 150px; background: var(--card-white); }
  .card--back  { left: 530px; top: 565px; background: var(--gold); }

  .card__shapes { position: absolute; inset: 0; }

  .brand-name {
    position: absolute;
    font-family: "Open Sans", Arial, sans-serif;
    font-weight: 600;
    white-space: nowrap;
    margin: 0;
  }
  .card--front .brand-name {
    right: 40px;
    top: 52px;
    font-size: 26px;
    color: var(--text-dark);
  }
  .card--back .brand-name {
    left: 0;
    right: 0;
    top: 136px;
    text-align: center;
    font-size: 38px;
    color: var(--paper);
  }

  .holder {
    position: absolute;
    left: 62px;
    top: 163px;
  }
  .holder__name {
    margin: 0;
    font-family: "Cinzel", Georgia, serif;
    font-weight: 700;
    font-size: 17px;
    letter-spacing: 0.5px;
    color: var(--gold);
    line-height: 1;
  }
  .holder__title {
    margin: 3px 0 0;
    font-size: 9.5px;
    color: var(--paper);
    line-height: 1.1;
  }

  .contacts {
    position: absolute;
    left: 62px;
    top: 216px;
    margin: 0;
    padding: 0;
    list-style: none;
  }
  .contacts__row {
    display: flex;
    align-items: center;
    gap: 8px;
    height: 24px;
    font-size: 12.5px;
    color: var(--text-dark);
    white-space: nowrap;
  }
  .contacts__item { display: flex; align-items: center; gap: 8px; margin-right: 14px; }
  .icon { width: 16px; height: 16px; flex: none; }
</style>
</head>
<body>
<main class="canvas">

  <section class="card card--front" aria-label="Business card front">
    <svg class="card__shapes" viewBox="0 0 560 320" aria-hidden="true">
      <rect x="0" y="165" width="560" height="155" fill="var(--gold)"/>
      <polygon points="0,150 228,150 300,165 232,206 0,206" fill="var(--ink)"/>
    </svg>

    <p class="brand-name">The Loom Briefing</p>

    <div class="holder">
      <p class="holder__name">BELINDA HARWICK</p>
      <p class="holder__title">Director and Stylist</p>
    </div>

    <ul class="contacts">
      <li class="contacts__row">
        <span class="contacts__item">
          <svg class="icon" viewBox="0 0 16 16" aria-hidden="true">
            <rect width="16" height="16" rx="3" fill="var(--icon-dark)"/>
            <path d="M5 3.5 L6.8 5.6 L5.8 6.8 Q7 9.2 9.2 10.2 L10.4 9.2 L12.5 11 L11.3 12.6 Q6.5 12 3.5 5 Z" fill="var(--paper)"/>
          </svg>
          +61 8 7142 5809
        </span>
        <span class="contacts__item">
          <svg class="icon" viewBox="0 0 16 16" aria-hidden="true">
            <rect width="16" height="16" rx="3" fill="var(--icon-dark)"/>
            <circle cx="8" cy="8" r="4.8" fill="none" stroke="var(--paper)" stroke-width="1"/>
            <ellipse cx="8" cy="8" rx="2" ry="4.8" fill="none" stroke="var(--paper)" stroke-width="0.9"/>
            <path d="M3.2 8 H12.8" stroke="var(--paper)" stroke-width="0.9"/>
          </svg>
          theloombriefing.example
        </span>
      </li>
      <li class="contacts__row">
        <svg class="icon" viewBox="0 0 16 16" aria-hidden="true">
          <rect x="1" y="3" width="14" height="10" fill="none" stroke="var(--icon-dark)" stroke-width="1.4"/>
          <path d="M1 3 L8 9 L15 3" fill="none" stroke="var(--icon-dark)" stroke-width="1.4"/>
        </svg>
        belinda@theloombriefing.example
      </li>
      <li class="contacts__row">
        <svg class="icon" viewBox="0 0 16 16" aria-hidden="true">
          <rect width="16" height="16" rx="3" fill="var(--icon-dark)"/>
          <path d="M4.2 8.3 L7 11 L12 5" fill="none" stroke="var(--paper)" stroke-width="1.6" stroke-linecap="round" stroke-linejoin="round"/>
        </svg>
        Corporate Workwear &amp; Uniform Specialist | Personal Stylist
      </li>
    </ul>
  </section>

  <section class="card card--back" aria-label="Business card back">
    <p class="brand-name">The Loom Briefing</p>
  </section>

</main>
</body>
</html>
```